Maris Dovey Studio Business Cards

Hi - using the information and logo provided I require a two sided business card designed with the following information. The business card is a 'mini card' 3.5" x 1.25".

Front of card should be the logo attached but inverted (so the background is the peach colour and the logo white).

Back should have these details. If we can't fit the Pictogrum and Friendwall part can we just put the little logos.

Tessa Varnold

Art and Design Consultant
Dealer - Curator - Events - Styling - Creative Sourcing

P: 0438 217 604
E: tessa@marisdoveystudio.example
W: www.marisdoveystudio.example
I (pictogram image please): marisdoveystudio F (Friendwall image please): MarisDoveyAdviser

Target Market(s)

Galleries, artists, art buyers, interior design clients, event managers, creative types

Industry/Entity Type

Business

```html
<!DOCTYPE html>
<html lang="en">
<head>
<meta charset="utf-8">
<title>Maris Dovey Studio — Mini Business Card</title>
<link rel="stylesheet" href="https://fonts.googleapis.com/css2?family=Libre+Baskerville&family=Arimo:wght@400&display=swap">
<style>
  :root {
    --backdrop: #8f8f8f;
    --peach: #f4bc9f;
    --paper: #ffffff;
    --slate: #67686f;
    --ink: #3f3f44;
    --serif: "Libre Baskerville", Georgia, serif;
    --sans: "Arimo", Arial, sans-serif;
  }
  * { margin: 0; padding: 0; box-sizing: border-box; }
  html, body { width: 1200px; height: 988px; overflow: hidden; }
  body { background: var(--backdrop); position: relative; font-family: var(--sans); }

  .card { position: absolute; left: 86px; width: 1027px; height: 366px; }
  .card--front { top: 102px; background: var(--peach); }
  .card--back { top: 539px; background: var(--paper); color: var(--ink); }

  .brand-mark {
    position: absolute; left: 50%; top: 62px; transform: translateX(-50%);
    width: 150px; height: 150px; border-radius: 50%; background: var(--paper);
  }
  .brand-name {
    position: absolute; left: 0; right: 0; top: 238px; text-align: center;
    font-family: var(--serif); font-size: 34px; letter-spacing: 0.18em;
    color: var(--slate); text-transform: uppercase;
  }

  .holder-name {
    position: absolute; left: 45px; top: 48px;
    font-family: var(--serif); font-size: 44px; color: var(--peach);
  }
  .holder-role, .holder-services {
    position: absolute; left: 45px; font-size: 25px; color: var(--ink);
  }
  .holder-role { top: 118px; }
  .holder-services { top: 162px; word-spacing: 0.12em; }

  .contact {
    position: absolute; right: 45px; text-align: right;
    font-size: 25px; color: var(--slate); line-height: 44px;
  }
  .contact--phone { top: 214px; letter-spacing: 0.08em; }
  .contact--email { top: 258px; }
  .contact--web { top: 302px; }

  .social {
    position: absolute; left: 45px; display: flex; align-items: center; gap: 20px;
    font-size: 25px; color: var(--slate); height: 44px;
  }
  .social--pictogram { top: 256px; }
  .social--friendwall { top: 300px; }
  .social__badge { width: 26px; height: 26px; background: var(--peach); flex: none; }
</style>
</head>
<body>
  <section class="card card--front" aria-label="Card front">
    <div class="brand-mark" aria-hidden="true"></div>
    <div class="brand-name">Maris Dovey Studio</div>
  </section>

  <section class="card card--back" aria-label="Card back">
    <h1 class="holder-name">Tessa Varnold</h1>
    <p class="holder-role">Art and Design Consultant</p>
    <p class="holder-services">Dealer - Curator - Events - Styling - Creative Sourcing</p>

    <p class="contact contact--phone">0438 217 604</p>
    <p class="contact contact--email">tessa@marisdoveystudio.example</p>
    <p class="contact contact--web">www.marisdoveystudio.example</p>

    <p class="social social--pictogram"><span class="social__badge" aria-hidden="true"></span>marisdoveystudio</p>
    <p class="social social--friendwall"><span class="social__badge" aria-hidden="true"></span>MarisDoveyAdviser</p>
  </section>
</body>
</html>
```